Heritage Hollow Business Cards

Require a business card design. <br/><br/>Needs to include logo (either round or long version) plus these details:<br/>Maya Torvell<br/>Heritage Hollow<br/>maya@kelvadtrading.com.au<br/>02 6481 7395<br/>PO Box Glenwarra NSW 2791<br/>www.heritagehollow.com.au<br/><br/>I need in an editable format so that I can create for multiple staff members. <br/><br/>

Target Market(s)

We are an online store selling renovation products to home owners are builders. Looking for a classic classy design.

Industry/Entity Type

Home And Garden

Contact Information for Business Card

Maya Torvell
Heritage Hollow
maya@kelvadtrading.com.au
02 6481 7395
PO Box Glenwarra NSW 2791
www.heritagehollow.com.au

Colors

Designer to choose colors to be used in the design.

Requirements
Must have
• Must include Logo.

```html
<!DOCTYPE html>
<html lang="en">
<head>
<meta charset="utf-8">
<title>Heritage Hollow Business Cards</title>
<link rel="stylesheet" href="https://fonts.googleapis.com/css2?family=Raleway:ital,wght@0,300;0,400;0,500;1,600&display=swap">
<style>
  :root {
    --backdrop: #e9e6e1;
    --card-dark: #262626;
    --card-light: #fbfbfb;
    --ink: #2b2b2b;
    --ink-soft: #3a3a3a;
    --ink-on-dark: #eeeeee;
  }
  * { margin: 0; padding: 0; box-sizing: border-box; }
  html, body {
    width: 1200px;
    height: 900px;
    overflow: hidden;
    background: var(--backdrop);
    font-family: "Raleway", sans-serif;
  }
  .sheet {
    position: relative;
    width: 1200px;
    height: 900px;
  }
  .card {
    position: absolute;
    left: 280px;
    width: 640px;
    height: 391px;
    border-radius: 2px;
    box-shadow: 0 6px 18px rgba(0,0,0,0.15);
  }
  .card--back {
    top: 48px;
    background: var(--card-dark);
    display: flex;
    align-items: center;
    justify-content: center;
  }
  .card--front {
    top: 462px;
    background: var(--card-light);
    color: var(--ink);
  }
  .brand {
    display: flex;
    align-items: center;
    gap: 14px;
    font-weight: 500;
    letter-spacing: 0.5px;
  }
  .brand__mark {
    width: 14px;
    height: 14px;
  }
  .card--back .brand {
    color: var(--ink-on-dark);
    font-size: 40px;
  }
  .card--back .brand__mark { background: var(--ink-on-dark); }
  .card--front .brand {
    position: absolute;
    left: 58px;
    top: 150px;
    color: var(--ink);
    font-size: 34px;
  }
  .card--front .brand__mark { background: var(--ink); }
  .holder {
    position: absolute;
    right: 46px;
    top: 46px;
    text-align: right;
  }
  .holder__name {
    font-weight: 300;
    font-size: 30px;
    letter-spacing: 1.5px;
    text-transform: uppercase;
    line-height: 1.1;
  }
  .holder__company {
    font-style: italic;
    font-weight: 600;
    font-size: 17px;
    color: var(--ink-soft);
    margin-top: 2px;
  }
  .contact {
    position: absolute;
    right: 46px;
    bottom: 40px;
    list-style: none;
    text-align: right;
    font-size: 18px;
    font-weight: 400;
    line-height: 1.38;
    color: var(--ink);
  }
</style>
</head>
<body>
  <main class="sheet">
    <section class="card card--back" aria-label="Card back">
      <div class="brand">
        <span class="brand__mark"></span>
        <span class="brand__name">Heritage Hollow</span>
      </div>
    </section>

    <section class="card card--front" aria-label="Card front">
      <div class="brand">
        <span class="brand__mark"></span>
        <span class="brand__name">Heritage Hollow</span>
      </div>

      <div class="holder">
        <p class="holder__name">Maya Torvell</p>
        <p class="holder__company">Heritage Hollow</p>
      </div>

      <ul class="contact">
        <li>maya@kelvadtrading.com.au</li>
        <li>02 6481 7395</li>
        <li>PO Box Glenwarra NSW 2791</li>
        <li>www.heritagehollow.com.au</li>
      </ul>
    </section>
  </main>
</body>
</html>
```